Online Dating Website called WinkAtWheel.com

PLEASE CAN ALL PARTICIPATING DESIGNERS PLEASE SUBMIT ALL PAGES AS DETAILED IN THE ORIGINAL BRIEF BELOW WITHIN 48 HOURS TO AVOID WINKATWHEEL EXTENDING THE CONTEST FURTHER.

We have an online dating website that is 95% fully functional and now require an exciting and creative designer to help us create the best dating experience. We are looking for your ideas on a couple of our key pages. These are our landing, profile and search page. We already have a homepage that we are happy with and winning designers will look to build upon the foundations of the homepage and extend them through their designs.

The premise of the site is the idea that if you've ever seen someone out driving and wished you could communicate because you found them attractive, how would you? Well with WinkAtWheel.com you can. Just enter their vehicle registration number (license plate) in to the website in order to get in touch, flirt and develop a relationship. It also allows users to find each other based on other criteria. It acts as both a specialist service and a normal dating website.

The pages that require developing are 1) our landing page, this is the page users see when they first login to the site, it comprises various pieces of information but it's primary function is a live feed of events generated based on the users favourited profiles and interactions with the user. 2) The profile page is the page where users can edit their own information, given the nature of this page we are looking for a creative design that gives this page some flair. 3) Finally we are looking for ideas for our search page, this page needs to provide a list of users who meet the user's search requirements and display the profile of a selected user.
Updates

Project Deadline Extended
Reason: We've asked for certain pages in our brief to be designed and this still hasn't been done. We've contacted the designers that have currently submitted designs and requested this several times. We still await for this to happen.

Target Market(s)

Male or Female age 18+

Industry/Entity Type

Dating

Requirements
Must have
• Our must have feature is a designer with an open mind. The functionality of the site must be present, all we ask is for you to be creative with the layout. Think out side of the box, change the colours, the layout, and the background as you feel. Make it look current and appealing to the user.
Nice to have
• Theme's carried through from the home page
Should not have
• Do not include Comic Sans or Times New Roman font in your designs.

```html
<!DOCTYPE html>
<html lang="en">
<head>
<meta charset="utf-8">
<title>winkatwheel – Profile</title>
<link href="https://fonts.googleapis.com/css2?family=Source+Sans+3:wght@300;400;600&display=swap" rel="stylesheet">
<style>
:root{
  --dark:#3b3b3b;
  --darker:#2a2a2a;
  --orange:#ff8a00;
  --pink:#e23d87;
  --lime:#b4c914;
  --cyan:#10bde0;
  --text:#444;
  --muted:#8a8a8a;
  --line:#dcdcdc;
  --panel-head:#ececec;
}
*{box-sizing:border-box;margin:0;padding:0}
html,body{width:1085px;height:1200px;overflow:hidden}
body{position:relative;background:#fff;font-family:"Source Sans 3",sans-serif;color:var(--text)}
.abs{position:absolute}

.site-header{position:absolute;left:0;top:0;width:1085px;height:100px;background:linear-gradient(#454545,#333);border-bottom:1px solid #222}
.brand{position:absolute;left:83px;top:28px;display:flex;align-items:center;gap:8px;color:#fff;font-size:31px;font-weight:400}
.brand-dot{width:28px;height:28px;border-radius:50%;background:var(--pink)}
.main-nav{position:absolute;left:0;top:35px;height:38px;font-size:15.5px;color:#fff}
.main-nav a{position:absolute;top:0;line-height:38px;color:#fff;text-decoration:none;white-space:nowrap}
.main-nav .active{background:#1f1f1f;border-radius:19px;width:76px;text-align:center}
.main-nav .sep{position:absolute;top:12px;width:1px;height:15px;background:#bbb}

.feature{position:absolute;border:1px solid var(--line);border-radius:10px;background:#fff;box-shadow:0 2px 3px rgba(0,0,0,.12);text-align:center;overflow:hidden}
.feature-top{position:absolute;left:0;top:0;width:100%;border-radius:0 0 50% 50%/0 0 18px 18px;display:flex;align-items:center;justify-content:center}
.feature h3{position:absolute;left:0;width:100%;font-size:20px;font-weight:400}
.feature p{position:absolute;left:18px;right:18px;font-size:11.5px;line-height:16px;color:var(--muted);font-weight:300}

.panel{position:absolute;left:284px;width:517px;border:1px solid var(--line);border-radius:10px;background:#fff;box-shadow:0 2px 3px rgba(0,0,0,.1)}
.panel-head{height:46px;border-radius:10px 10px 0 0;background:linear-gradient(#f6f6f6,#e2e2e2);border-bottom:1px solid #ccc;padding:12px 23px;font-size:20px;font-weight:400;color:#555}
.panel-head.soft{background:var(--panel-head);border-bottom:none;color:var(--pink);height:42px;padding:10px 24px}
.photo{position:absolute;border-radius:8px;border:3px solid #f1f1f1;box-shadow:0 0 0 1px #ddd}
.lead-name{position:absolute;left:155px;top:78px;font-size:20px;color:#333}
.lead-meta{position:absolute;left:155px;font-size:12.5px;line-height:17px;color:#333}
.lead-body{position:absolute;left:157px;width:345px;font-size:12.5px;line-height:18.5px;color:#666;font-weight:300}

.member{position:absolute;left:24px;width:470px;height:110px}
.member .photo{left:0;top:0;width:104px;height:101px}
.member h4{position:absolute;left:115px;top:6px;font-size:14px;font-weight:400;color:#333}
.member .loc{position:absolute;left:115px;top:24px;font-size:13px;color:#444}
.member p{position:absolute;left:115px;top:44px;width:340px;font-size:11.5px;line-height:19.5px;color:#666;font-weight:300}

.more-btn{position:absolute;left:636px;top:987px;width:164px;height:33px;border-radius:9px;background:linear-gradient(#b3b3b3,#8d8d8d);color:#fff;font-size:13.5px;display:flex;align-items:center;justify-content:center;gap:6px;box-shadow:0 1px 2px rgba(0,0,0,.3)}

.chat-tab{position:absolute;left:1039px;top:379px;width:46px;height:160px;background:linear-gradient(90deg,#3a3a3a,#4c4c4c);border:1px solid #222;border-right:none;border-radius:4px 0 0 4px;color:#fff}
.chat-tab span{position:absolute;left:50%;top:60px;transform:translate(-50%,-50%) rotate(-90deg);font-size:17px;font-weight:600;white-space:nowrap;letter-spacing:.5px}

.site-footer{position:absolute;left:0;top:1059px;width:1085px;height:141px;background:linear-gradient(#3e3e3e,#2b2b2b);border-top:1px solid #222;color:#fff}
.foot-col{position:absolute;top:22px;list-style:none;font-size:13px;line-height:25.7px}
.foot-col li::before{content:"»";margin-right:6px}
.foot-brand{position:absolute;left:768px;top:30px;display:flex;align-items:center;gap:8px;font-size:29px}
.foot-brand .brand-dot{background:#ccc;width:26px;height:26px}
.copy{position:absolute;right:101px;text-align:right;font-size:13px}
.social{position:absolute;top:79px;width:32px;height:32px;border-radius:3px}
</style>
</head>
<body>

<header class="site-header">
  <div class="brand">winkatwheel<span class="brand-dot"></span></div>
  <nav class="main-nav">
    <a style="left:408px">Home</a>
    <a class="active" style="left:467px">Profile</a>
    <a style="left:565px">Messages</a><span class="sep" style="left:646px"></span>
    <a style="left:665px">Matches</a><span class="sep" style="left:738px"></span>
    <a style="left:758px">Search</a><span class="sep" style="left:821px"></span>
    <a style="left:840px">Support</a><span class="sep" style="left:912px"></span>
    <a style="left:931px">My Account</a>
  </nav>
</header>

<!-- left features -->
<section class="feature" style="left:73px;top:130px;width:193px;height:212px">
  <div class="feature-top" style="height:104px;background:var(--orange)">
    <svg width="56" height="56" viewBox="0 0 56 56"><circle cx="23" cy="23" r="15" fill="none" stroke="#fff" stroke-width="6"/><line x1="33" y1="33" x2="48" y2="48" stroke="#fff" stroke-width="8" stroke-linecap="round"/><path d="M14 22a9 9 0 0 1 9-9" stroke="#fff" stroke-width="3" fill="none"/></svg>
  </div>
  <h3 style="top:115px;color:var(--orange)">Find Now</h3>
  <p style="top:143px">Vivamus porttitor, g, purus nisi eleifend libero, a tempus libero lectus feugiat felis diam</p>
</section>

<section class="feature" style="left:78px;top:356px;width:188px;height:204px">
  <div class="feature-top" style="height:99px;background:var(--pink)">
    <svg width="66" height="66" viewBox="0 0 66 66"><path d="M18 48h-2a12 12 0 0 1 0-24 17 17 0 0 1 33-3 13 13 0 0 1 2 27h-3" fill="none" stroke="#fff" stroke-width="6" stroke-linejoin="round" stroke-linecap="round"/><path d="M33 64V34M23 43l10-10 10 10" fill="none" stroke="#fff" stroke-width="6" stroke-linecap="round" stroke-linejoin="round"/></svg>
  </div>
  <h3 style="top:110px;color:var(--pink)">Sign Up</h3>
  <p style="top:136px">Vivamus porttitor, g, purus nisi eleifend libero, a tempus libero lectus feugiat felis diam</p>
</section>

<!-- right features -->
<section class="feature" style="left:825px;top:136px;width:187px;height:205px">
  <div class="feature-top" style="height:100px;background:var(--lime)">
    <svg width="66" height="56" viewBox="0 0 66 56"><path d="M30 50 8 28A13 13 0 0 1 30 12 13 13 0 0 1 52 22" fill="none" stroke="#fff" stroke-width="5" stroke-linejoin="round"/><circle cx="48" cy="38" r="12" fill="#fff"/><path d="M48 31v14M41 38h14" stroke="var(--lime)" stroke-width="4"/></svg>
  </div>
  <h3 style="top:111px;color:var(--lime)">Get Connect</h3>
  <p style="top:137px">Vivamus porttitor, g, purus nisi eleifend libero, a tempus libero lectus feugiat felis diam</p>
</section>

<section class="feature" style="left:826px;top:354px;width:186px;height:202px">
  <div class="feature-top" style="height:98px;background:var(--cyan)">
    <svg width="62" height="62" viewBox="0 0 62 62"><circle cx="31" cy="31" r="27" fill="none" stroke="#fff" stroke-width="5"/><path d="M31 46 18 33a8 8 0 0 1 13-10 8 8 0 0 1 13 10Z" fill="#fff"/></svg>
  </div>
  <h3 style="top:109px;color:var(--cyan)">Dating</h3>
  <p style="top:135px">Vivamus porttitor, g, purus nisi eleifend libero, a tempus libero lectus feugiat felis diam</p>
</section>

<aside class="chat-tab">
  <span>OPEN CHAT</span>
  <svg class="abs" style="left:11px;top:124px" width="26" height="24" viewBox="0 0 26 24"><path d="M3 2h14a2 2 0 0 1 2 2v7a2 2 0 0 1-2 2H9l-5 4v-4H3a2 2 0 0 1-2-2V4a2 2 0 0 1 2-2Z" fill="#fff"/><path d="M21 8h2a2 2 0 0 1 2 2v7a2 2 0 0 1-2 2h-1v4l-5-4h-6a2 2 0 0 1-2-2v-2h8a3 3 0 0 0 3-3Z" fill="#ddd"/></svg>
</aside>

<!-- latest profile -->
<section class="panel" style="top:131px;height:318px">
  <div class="panel-head">Latest Profile</div>
  <div class="photo" role="img" aria-label="Portrait photo of the latest member" style="left:18px;top:61px;width:121px;height:122px;background:linear-gradient(135deg,#a8c68a,#c89a78 55%,#7a9a60)"></div>
  <div class="lead-name">Person Name</div>
  <div class="lead-meta" style="top:104px;font-size:11px">View my: Photos / Vidoes</div>
  <div class="lead-meta" style="top:124px">Age: 18 &nbsp;&nbsp; MALE<br>Melbourne, Vicotiral, AU<br>Last Login: 07/08/2013</div>
  <p class="lead-body" style="top:179px">Vivamus porttitor, g, purus nisi eleifend libero, a tempus libero lectus feugiat felis. Morbi diam mauris, viverra in, gravida eu, mattis in, ante. Morbi eget arcu.</p>
  <p class="lead-body" style="top:255px">Morbi porta, libero id ullamcorper nonummy, nibh ligula pulvinar metus, eget consectetuer augue nisi quis lacus.</p>
</section>

<!-- more profiles -->
<section class="panel" style="top:460px;height:545px">
  <div class="panel-head soft">More Profiles</div>
  <div class="member" style="top:54px">
    <div class="photo" role="img" aria-label="Member portrait photo" style="background:linear-gradient(135deg,#9a9a9a,#c59a80 50%,#6a5a50)"></div>
    <h4>Person Name</h4><div class="loc">Location</div>
    <p>Vivamus porttitor, g, purus nisi eleifend libero, a tempus libero lectus feugiat felis. Morbi diam mauris, viverra in, gravida eu, mattis in, ante. Morbi eget arcu.</p>
  </div>
  <div class="member" style="top:172px">
    <div class="photo" role="img" aria-label="Member portrait photo" style="background:linear-gradient(135deg,#f2f2f2,#c8a08a 50%,#3a3a3a)"></div>
    <h4>Person Name</h4><div class="loc">Location</div>
    <p>Vivamus porttitor, g, purus nisi eleifend libero, a tempus libero lectus feugiat felis. Morbi diam mauris, viverra in, gravida eu, mattis in, ante. Morbi eget arcu.</p>
  </div>
  <div class="member" style="top:292px">
    <div class="photo" role="img" aria-label="Member portrait photo" style="background:linear-gradient(135deg,#e6e0d6,#c49a7a 50%,#5a6a30)"></div>
    <h4>Person Name</h4><div class="loc">Location</div>
    <p>Vivamus porttitor, g, purus nisi eleifend libero, a tempus libero lectus feugiat felis. Morbi diam mauris, viverra in, gravida eu, mattis in, ante. Morbi eget arcu.</p>
  </div>
  <div class="member" style="top:410px">
    <div class="photo" role="img" aria-label="Member portrait photo" style="background:linear-gradient(135deg,#2a2a2a,#c8a088 50%,#3a3030)"></div>
    <h4>Person Name</h4><div class="loc">Location</div>
    <p>Vivamus porttitor, g, purus nisi eleifend libero, a tempus libero lectus feugiat felis. Morbi diam mauris, viverra in, gravida eu, mattis in, ante. Morbi eget arcu.</p>
  </div>
</section>
<div class="more-btn">View More Profiles <svg width="6" height="9" viewBox="0 0 6 9"><path d="M0 0l6 4.5L0 9Z" fill="#fff"/></svg></div>

<footer class="site-footer">
  <ul class="foot-col" style="left:107px"><li>Home</li><li>Mobile Site</li><li>Friendnest</li><li>Chirpline</li></ul>
  <ul class="foot-col" style="left:236px"><li>General Conditions</li><li>Terms &amp; Conditions</li><li>Privacy Statement</li><li>Cookies Information</li></ul>
  <ul class="foot-col" style="left:420px"><li>Contact us</li><li>FAQ's &amp; Help</li><li>Safe Dating Advice</li><li>Pricing Details</li></ul>
  <div class="foot-brand">winkatwheel<span class="brand-dot"></span></div>
  <div class="copy" style="top:72px">Copyright © 2013 &nbsp;Wink At Wheel</div>
  <div class="copy" style="top:98px">All rights reserved.</div>
  <div class="social" style="left:654px;background:#3b5a9a"></div>
  <div class="social" style="left:701px;background:#3fb5e6"></div>
  <div class="social" style="left:749px;background:#1a7ab5"></div>
</footer>

</body>
</html>
```